A Gallery type Web design

We are developing a Wordpress based website for a client that does design construction projects. E.g. Pools, Lobbies, Toilets, etc. The website will mainly be to showcase their past projects and the collections they have.
No programming required, we just need the designs!
A sample of what the client is looking for:
http://velmorati.it/
Pages to include:
• Home – A nice slider design to showcase selected photos
• Main Category Template
• Sub Category Template
• About us
• Contact us
Example of their Main Categories and their Sub Categories:
Collections - Granite
- Marble
- Sculpture
Projects - Private
- Public
- Commercial
- Overseas
Installation - Vanity tops
- Hall areas
- Toilets
The Main Category is to show a sample and link the user to the respective Sub Categories. The Sub Categories are to showcase all the photos they have from the category. Please leave a little space to add some text or caption for the photo.
Designs need to be mobile responsive!
I've attached their logo and some sample photos to use for mock ups. Let me know if you have any questions!

```html
<!DOCTYPE html>
<html lang="en">
<head>
<meta charset="utf-8">
<title>Granvale Stone — Home</title>
<link rel="stylesheet" href="https://fonts.googleapis.com/css2?family=Raleway:wght@400;500;600&family=Open+Sans:ital,wght@0,400;0,600;1,400&display=swap">
<style>
  :root {
    --header-bg: #a8a8a8;
    --ink: #1b1b1b;
    --white: #ffffff;
    --content-bg: #000000;
    --footer-bg: #1c1c1c;
    --muted: #9a9a9a;
    --soft: #c9c9c9;
    --accent: #e8321f;
    --button-top: #5a5a5a;
    --button-bottom: #3a3a3a;
  }
  * { box-sizing: border-box; margin: 0; padding: 0; }
  html, body { width: 1200px; height: 879px; overflow: hidden; background: var(--content-bg); }
  body { position: relative; font-family: "Open Sans", Arial, sans-serif; }

  .site-header { position: absolute; left: 0; top: 0; width: 1200px; height: 110px; background: var(--header-bg); }
  .brand { position: absolute; left: 140px; top: 38px; display: flex; align-items: center; gap: 10px;
    font-family: "Raleway", sans-serif; font-weight: 600; font-size: 20px; color: var(--ink); letter-spacing: 1px; }
  .brand-mark { width: 18px; height: 18px; background: var(--ink); }
  .search { position: absolute; left: 798px; top: 19px; width: 200px; height: 27px; background: #e4e4e4;
    border: 1px solid #cfcfcf; }
  .search span { position: absolute; left: 11px; top: 6px; font-size: 10px; font-style: italic; color: #777; }
  .search svg { position: absolute; right: 9px; top: 5px; }
  .main-nav { position: absolute; right: 202px; top: 70px; display: flex; align-items: center;
    font-family: "Raleway", sans-serif; font-size: 13.5px; font-weight: 500; color: var(--ink); }
  .main-nav a { color: inherit; text-decoration: none; padding: 0 16px; border-left: 1px solid #7c7c7c; line-height: 18px; }
  .main-nav a:first-child { border-left: 0; }
  .main-nav a:last-child { padding-right: 0; }

  .hero { position: absolute; left: 0; top: 110px; width: 1200px; height: 488px;
    background: radial-gradient(ellipse at 62% 30%, #b8aa93 0%, #6e6458 30%, #2f2a25 65%, #141210 100%); }
  .hero-caption { position: absolute; left: 318px; top: 172px; width: 570px; height: 128px;
    background: rgba(12,12,12,0.72); text-align: center; color: var(--white); font-family: "Raleway", sans-serif; }
  .hero-title { margin-top: 20px; font-size: 41px; font-weight: 600; line-height: 46px; letter-spacing: 0.3px; }
  .hero-subtitle { font-size: 22.5px; font-weight: 400; line-height: 26px; }
  .hero-arrow { position: absolute; top: 208px; }
  .hero-arrow.prev { left: 120px; }
  .hero-arrow.next { left: 1046px; }

  .intro { position: absolute; left: 138px; top: 633px; width: 450px; }
  .intro h1 { font-family: "Raleway", sans-serif; font-weight: 500; font-size: 19.5px; color: var(--white); line-height: 24px; }
  .intro .lead { margin-top: 7px; font-size: 14px; color: var(--soft); line-height: 20px; }
  .intro p { margin-top: 3px; font-size: 11px; color: var(--muted); line-height: 16px; }
  .intro p + p { margin-top: 8px; }

  .project-photo { position: absolute; left: 631px; top: 642px; width: 177px; height: 130px;
    background: linear-gradient(135deg, #5c5a57 0%, #2c2b2a 45%, #8a5a2e 70%, #d9cfc0 100%); }
  .recent { position: absolute; left: 822px; top: 636px; width: 240px; }
  .recent h2 { font-family: "Raleway", sans-serif; font-weight: 500; font-size: 20px; color: var(--accent); line-height: 24px; }
  .recent p { margin-top: 8px; font-size: 11px; color: var(--muted); line-height: 17.5px; }
  .button { display: inline-block; margin-top: 12px; margin-left: 2px; width: 86px; height: 25px; line-height: 25px;
    text-align: center; font-size: 9px; font-weight: 600; color: var(--white); border-radius: 2px;
    background: linear-gradient(var(--button-top), var(--button-bottom)); }

  .site-footer { position: absolute; left: 0; top: 820px; width: 1200px; height: 59px; background: var(--footer-bg);
    font-size: 11px; color: #bdbdbd; }
  .copyright { position: absolute; left: 136px; top: 21px; }
  .social { position: absolute; left: 466px; top: 20px; display: flex; gap: 10px; }
  .social span { width: 14px; height: 14px; border-radius: 50%; background: #e0e0e0; }
  .footer-nav { position: absolute; left: 590px; top: 21px; display: flex; }
  .footer-nav a { color: inherit; text-decoration: none; }
  .footer-nav i { font-style: normal; padding: 0 10px; }
</style>
</head>
<body>
  <header class="site-header">
    <div class="brand"><span class="brand-mark"></span>GRANVALE STONE</div>
    <div class="search">
      <span>Search here..</span>
      <svg width="16" height="16" viewBox="0 0 16 16"><circle cx="6.5" cy="6.5" r="4.8" fill="none" stroke="#fff" stroke-width="2"/><line x1="10" y1="10" x2="14.5" y2="14.5" stroke="#fff" stroke-width="2.4" stroke-linecap="round"/></svg>
    </div>
    <nav class="main-nav">
      <a href="#">HOME</a><a href="#">COLLECTIONS</a><a href="#">PROJECTS</a><a href="#">INSTALLATIONS</a><a href="#">ABOUT US</a><a href="#">CONTACT US</a>
    </nav>
  </header>

  <section class="hero" role="img" aria-label="Slider photo of a lamp-lit lobby with dining chairs, console table and mosaic floor">
    <div class="hero-caption">
      <div class="hero-title">POOLS &amp; LOBBIES STONE</div>
      <div class="hero-subtitle">VITAE FELIS VESTIBULUM VOLUTPAT</div>
    </div>
    <svg class="hero-arrow prev" width="34" height="68" viewBox="0 0 34 68"><polyline points="32,2 2,34 32,66" fill="none" stroke="#fff" stroke-width="2"/></svg>
    <svg class="hero-arrow next" width="34" height="68" viewBox="0 0 34 68"><polyline points="2,2 32,34 2,66" fill="none" stroke="#fff" stroke-width="2"/></svg>
  </section>

  <section class="intro">
    <h1>WELCOME TO GRANVALE STONE MAINPAGE</h1>
    <div class="lead">Etiam est nunc venenatis in tristique eu imperdiet ac nisl</div>
    <p>et magnis dis parturient montes nascetur ridiculus mus feugiat felis Morbi diam iaculis facilisis massa Etiam eu urnafeugiat felis Morbi diam mauris viverra</p>
    <p>Morbi ornare gravida elit Integer congue augue et malesuada iaculis ipsum dui aliquet felis at cursus magna nisl nec elit Praesent elementum elit at tellus nec ultricies sit amet porttitor mattis enim In massa libero interdum end libero a tempus libero</p>
  </section>

  <div class="project-photo" role="img" aria-label="Photo of a mosaic-tiled fireplace wall with a woven bowl"></div>
  <section class="recent">
    <h2>RECENT PROJECTS</h2>
    <p>Curabitur iaculis tempus eros Curabitur vel mi sit amet magna malesuada ultrices Ut nisi erat fermentum vel congue id euismod in elit Fusce ultricies orci ac end libero a tempus lib</p>
    <a class="button">VIEW MORE</a>
  </section>

  <footer class="site-footer">
    <div class="copyright">© 2014 COMPANY NAME &nbsp;ALL RIGHT RESERVED &nbsp;TERM OF USE</div>
    <div class="social" aria-label="Social links"><span></span><span></span><span></span></div>
    <nav class="footer-nav">
      <a href="#">HOME</a><i>|</i><a href="#">COLLECTIONS</a><i>|</i><a href="#">PROJECTS</a><i>|</i><a href="#">INSTALLATIONS</a><i>|</i><a href="#">ABOUT US</a><i>|</i><a href="#">CONTACT US</a>
    </nav>
  </footer>
</body>
</html>
```